"Copper Lantern" Play - Poster Design for Theatre Group

We are an amateur theatre group based in Geneva, Switzerland. We take pride in eye-catching posters for our shows, which are printed in various sizes.
This design will be for a play in March 2016. The play is called "Copper Lantern", and it's a Marwick Medal winner from Martin Crowe-Fenwick. The play is about a couple who have everything a family could want, until they lose a child in a life-shattering accident that turns their world upside down. The play charts the couple's bittersweet search to find each other and to find comfort.
Most importantly, we want a design that will make people want to see the show. We don't want to give away the plot or be too heavy-handed about death, but we want it to be clear that it's not a comedy (although there are some lighter moments!).
Attached you will find a template for the poster. This simply has our group name and logo in the top right corner: (Lakeside Stage Players Guild presents).
You may change the color of both the text and the logo, but please do not change the font, size, or location.
Here is the information that needs to be on the poster, wherever you see fit:
play title: Copper Lantern
author byline: by Martin Crowe-Fenwick
director line: directed by Ned Pilbury
tagline: How do you keep it together when your whole world's fallen apart?
dates and times:
1-5 March 2016
(Tue-Fri 20:00, Sat 19:00)
location:
Théâtre du Colibri
Eaux-Vives, Geneva
websites:
www.lspg.ch
www.scenesansfrontiere.ch
Technical Details:
Any font or combination of fonts is acceptable. The largest text should be the play title. The author's name must be at least 50% of the title font size.
For this competition, we would like the version with A3 proportions, which will also be used at F4 (89.5 x 128 cm) and A5 sizes (14.8 x 21 cm). Therefore no text should be below 9pt at A5.
However, from the winning designer we will also need repurposed sizes of the same design. Here is a comprehensive list of the sizes we will need.
1) A3 print poster. Artwork should be 300dpi, CMYK, sent with a 1mm bleed all round, to specification PDF/X-1A:2001. We will need this image in PDF format in addition to the default Artmarketo formats.
2) Chatterbook advert picture. 1200px by 628px, RGB jpeg. This must comply with Chatterbook’s restrictions on amount of text, which is no more than 20% of area taken up by text.(https://www.chatterbook-example.com/ads/tools/text_overlay).
Because of these restrictions it is sufficient to include just the title and the author's name in this version.
3) Chatterbook cover picture: 851px by 314px. RGB jpeg. It is sufficient to include just the title and the author's name in this version.
4) Web banner. 1000px by 300px. RGB jpeg. This version should include just the main image(s), no text.

```html
<!DOCTYPE html>
<html lang="en">
<head>
<meta charset="utf-8">
<title>Copper Lantern – Poster</title>
<link href="https://fonts.googleapis.com/css2?family=Cinzel:wght@400;500&family=Roboto:wght@400;500;700&display=swap" rel="stylesheet">
<style>
  :root {
    --backdrop: #dcdcdc;
    --paper: #f7f7f7;
    --ink: #1a1a1a;
    --rust: #c4572e;
    --muted: #6f6f6f;
    --band: #0d0d0d;
    --band-text: #ffffff;
    --accent: #e8892f;
    --photo-light: #ffffff;
    --photo-dark: #0c0c0c;
  }
  * { margin: 0; padding: 0; box-sizing: border-box; }
  html, body { width: 960px; height: 1200px; overflow: hidden; }
  body {
    background: var(--backdrop);
    display: flex;
    align-items: center;
    justify-content: center;
  }
  .poster {
    position: relative;
    width: 780px;
    height: 1103px;
    background: var(--paper);
    overflow: hidden;
    font-family: "Cinzel", serif;
    color: var(--ink);
  }
  .presenter {
    position: absolute;
    top: 60px;
    right: 44px;
    display: flex;
    align-items: center;
    gap: 14px;
  }
  .presenter-name {
    font-family: "Roboto", sans-serif;
    font-weight: 500;
    font-size: 19px;
    line-height: 1.25;
    text-align: right;
    color: var(--ink);
  }
  .presenter-mark {
    width: 96px;
    height: 96px;
    border-radius: 50%;
    border: 3px solid var(--ink);
  }
  .title {
    position: absolute;
    top: 200px;
    left: 0;
    width: 100%;
    text-align: center;
    font-weight: 400;
    font-size: 100px;
    line-height: 1;
    letter-spacing: 1px;
    color: var(--rust);
  }
  .title span { display: block; }
  .credits {
    position: absolute;
    top: 412px;
    left: 0;
    width: 100%;
    text-align: center;
    color: var(--muted);
  }
  .credits .author-line {
    display: block;
    font-size: 50px;
    line-height: 1.1;
    white-space: nowrap;
  }
  .credits .director-line {
    display: block;
    font-size: 24px;
    line-height: 1.3;
  }
  .credits .role { font-size: 22px; }
  .tagline {
    position: absolute;
    top: 516px;
    left: 0;
    width: 100%;
    text-align: center;
    font-size: 22px;
    line-height: 1.55;
    color: var(--ink);
  }
  .key-image {
    position: absolute;
    top: 600px;
    left: 56px;
    width: 668px;
    height: 380px;
    background:
      radial-gradient(ellipse 48% 50% at 50% 62%, var(--photo-dark) 0%, var(--photo-dark) 45%, #5a5a5a 65%, var(--photo-light) 100%);
  }
  .info-band {
    position: absolute;
    left: 0;
    bottom: 0;
    width: 100%;
    height: 123px;
    background: var(--band);
    font-family: "Roboto", sans-serif;
    text-align: center;
    padding-top: 18px;
  }
  .dates {
    font-weight: 700;
    font-size: 25px;
    color: var(--band-text);
  }
  .venue {
    margin-top: 8px;
    font-size: 19px;
    color: var(--accent);
    letter-spacing: 0.3px;
  }
  .websites {
    margin-top: 7px;
    font-size: 18px;
    color: var(--band-text);
    letter-spacing: 1px;
  }
</style>
</head>
<body>
  <main class="poster">
    <header class="presenter">
      <p class="presenter-name">Lakeside Stage<br>Players Guild<br>presents</p>
      <div class="presenter-mark" aria-hidden="true"></div>
    </header>

    <h1 class="title"><span>Copper</span><span>Lantern</span></h1>

    <p class="credits">
      <span class="author-line"><span class="role">by</span> Martin Crowe-Fenwick</span>
      <span class="director-line"><span class="role">Directed by</span> Ned Pilbury</span>
    </p>

    <p class="tagline">How do you keep it together<br>when your whole world's fallen apart?</p>

    <div class="key-image" role="img" aria-label="Black silhouette of a grieving couple crouched back to back, heads in hands, on a white background"></div>

    <footer class="info-band">
      <p class="dates">1-5 MARCH 2016 (TUE-FRI 20:00, SAT 19:00)</p>
      <p class="venue">LOCATION: THÉÂTRE DU COLIBRI, EAUX-VIVES, GENEVA</p>
      <p class="websites">websites: www.lspg.ch &nbsp;|&nbsp; www.scenesansfrontiere.ch</p>
    </footer>
  </main>
</body>
</html>
```